Yacht, Boats, Watersports company needs a redesign of business card

Hello Designers!
We are a Boat dealership company that sells fun in the water, we sell boats, Yachts, Kayaks and also yacht WaterSport toys. We are looking to redesign our business cards in to something a little bit more sophisticated. in a way that we can make better use of our company colors. I'm attaching a zipped file containing the company 3 sets of company logo which one is an horizontal another one is a vertical and also a chromed 3d logo. Also is included two set of business cards that we use and also some designs that i think it's interesting. We use PMS 2026c Orange and PMS 7687C Blue. I would like to see at least two different options with the orange as accent and also using blue as an accent color. It's really important for the business cards to have a font option and size that is legible to most people. Our current website is wwww.coralpennant.com. Please visit if you want to have a better feeling of the Boat dealership
You can send Single sided or double side options. We are now using single sided but we may be open for a double side option if we really like the design.
Target Market(s)
Marine, boat sales, yacht sales, water toys sales/
Contact Information for Business Card
Name: Dale Whitcombe
Address: 212 North Fenwick Lane,
Marlin Key, FL 33071
Phone: 954-731-8842
Fax: 954:731-8843
Cell: 954-382-1490
Email: dw@coralpennant.com
Website: coralpennant.com
Requirements
Must have
- the current information of the business card provided.
logo
use the PMS Colors
Nice to have
- a touch of elegance and sophistication but simple
Should not have
- should not have any typography that is hard to read, the card should be simple but yet sophisticated.

```html
<!DOCTYPE html>
<html lang="en">
<head>
<meta charset="utf-8">
<title>Coral Pennant – Business Card</title>
<link href="https://fonts.googleapis.com/css2?family=Audiowide&family=Roboto:wght@400;500;700&display=swap" rel="stylesheet">
<style>
  :root {
    --stage: #a3a3a3;
    --navy: #0d4a80;
    --brand-blue: #12437a;
    --brand-orange: #f15a29;
    --ink: #333333;
    --rule: #c8c8c8;
    --paper: #ffffff;
  }
  * { box-sizing: border-box; margin: 0; padding: 0; }
  html, body { width: 1200px; height: 1200px; overflow: hidden; }
  body { background: var(--stage); position: relative; font-family: "Roboto", Arial, sans-serif; }

  .card {
    position: absolute;
    top: 305px;
    width: 370px;
    height: 598px;
    border-radius: 14px;
    overflow: hidden;
  }
  .card--back { left: 202px; background: var(--navy); }
  .card--front { left: 602px; background: var(--paper); }

  .back-pattern { position: absolute; inset: 0; width: 100%; height: 100%; }

  .back-name {
    position: absolute;
    left: 0; right: 0;
    top: 507px;
    text-align: center;
    font-family: "Audiowide", sans-serif;
    font-size: 21px;
    letter-spacing: 1px;
    color: #ffffff;
    line-height: 26px;
  }

  .brand-dot {
    position: absolute;
    left: 148px; top: 105px;
    width: 72px; height: 72px;
  }
  .brand-name {
    position: absolute;
    left: 0; right: 0;
    top: 190px;
    text-align: center;
    font-family: "Audiowide", sans-serif;
    font-size: 21px;
    letter-spacing: 1px;
    line-height: 26px;
    color: var(--brand-blue);
  }

  .person {
    position: absolute;
    left: 0; right: 0;
    top: 320px;
    text-align: center;
    font-family: "Audiowide", sans-serif;
    font-size: 19px;
    font-weight: 400;
    letter-spacing: 1px;
    line-height: 24px;
  }
  .person__first { color: var(--brand-blue); margin-right: 8px; }
  .person__last { color: var(--brand-orange); }

  .rule {
    position: absolute;
    left: 117px;
    width: 132px;
    height: 1px;
    background: var(--rule);
  }
  .rule--top { top: 355px; }
  .rule--bottom { top: 498px; }

  .contact {
    position: absolute;
    left: 0; right: 0;
    top: 370px;
    list-style: none;
    text-align: center;
    font-size: 17px;
    line-height: 21.6px;
    color: var(--ink);
  }
  .contact b { color: var(--brand-blue); font-weight: 700; }
  .contact .web-name { color: var(--brand-blue); }

  .address {
    position: absolute;
    left: 0; right: 0;
    top: 507px;
    text-align: center;
    font-size: 17px;
    line-height: 21.6px;
    color: var(--ink);
    font-style: normal;
  }
</style>
</head>
<body>
  <section class="card card--back">
    <svg class="back-pattern" role="img" aria-label="Faint repeating brand-mark pattern on navy" viewBox="0 0 370 598" preserveAspectRatio="none">
      <defs>
        <radialGradient id="backGlow" cx="50%" cy="55%" r="70%">
          <stop offset="0%" stop-color="#13538f"/>
          <stop offset="100%" stop-color="#0b4477"/>
        </radialGradient>
      </defs>
      <rect width="370" height="598" fill="url(#backGlow)"/>
    </svg>
    <p class="back-name">CORAL PENNANT</p>
  </section>

  <section class="card card--front">
    <svg class="brand-dot" viewBox="0 0 72 72" aria-hidden="true">
      <circle cx="36" cy="36" r="32" fill="none" stroke="var(--brand-orange)" stroke-width="7"/>
    </svg>
    <p class="brand-name">CORAL PENNANT</p>

    <h1 class="person"><span class="person__first">DALE</span><span class="person__last">WHITCOMBE</span></h1>
    <div class="rule rule--top"></div>

    <ul class="contact">
      <li><b>P:</b> 954-731-8842</li>
      <li><b>F:</b> 954:731-8843</li>
      <li><b>M:</b> 954-382-1490</li>
      <li><b>P:</b> dw@coralpennant.com</li>
      <li>www.<span class="web-name">coralpennant</span>.com</li>
    </ul>

    <div class="rule rule--bottom"></div>

    <address class="address">212 North Fenwick Lane<br>Marlin Key, FL 33071</address>
  </section>
</body>
</html>
```